Wandering Rooms Stationary Set

Wandering Rooms is a bespoke interior design firm set to provide services to VIP clients with elegance and minimalism is the main theme for our stationary set. We require a full stationary set covering A4 letterhead, A4 & A3 envelopes, business cards, USB's, CDs, email signature and any other item the designer sees fit. logo is already designed and finalized, and we require the designer to use it as is without modifying the logo.

Address to be used on letterhead / business cards ...etc shall be as follows:

Phone : +971 2 518 2047
P.O. Box : 309186
Address: Block C&D, Bldg. 47, Court 12, Abu Dhabi, United Arab Emirates
Website: www.wanderingrooms-example.com

Target Market(s)

VIP Clients

Industry/Entity Type

Interior Design

Font styles to use
Other font styles liked:
• something to be unique

Colors

Designer to choose colors to be used in the design.

Requirements
Must have
• Elegant, minimalistic
Nice to have
• Simple yet elegant design having a sharp yet clean cut format
Should not have
• No additional colours, just colours that are used in the logo (silver, black or gold)

```html
<!DOCTYPE html>
<html lang="en">
<head>
<meta charset="utf-8">
<title>Wandering Rooms – Business Card</title>
<link rel="stylesheet" href="https://fonts.googleapis.com/css2?family=Cormorant+Garamond:wght@500&family=Roboto:wght@400&display=swap">
<style>
  :root {
    --backdrop: #3a2a22;
    --card: #0d0d0d;
    --silver: #c9c7c2;
    --silver-dim: #a9a7a2;
    --gold-edge: #8a7550;
  }
  * { box-sizing: border-box; margin: 0; padding: 0; }
  html, body { width: 1200px; height: 787px; overflow: hidden; }
  body {
    background: var(--backdrop);
    display: flex;
    align-items: center;
    justify-content: center;
    gap: 40px;
  }
  .card {
    position: relative;
    width: 540px;
    height: 310px;
    background: var(--card);
    box-shadow: 0 6px 18px rgba(0,0,0,.45);
    color: var(--silver);
  }
  .card--back { border-bottom: 1px solid var(--gold-edge); border-left: 1px solid var(--gold-edge); }

  .brand-name {
    font-family: "Cormorant Garamond", serif;
    font-weight: 500;
    color: var(--silver);
    letter-spacing: 1px;
    white-space: nowrap;
  }

  /* front */
  .front-brand {
    position: absolute; left: 0; right: 0; top: 108px;
    text-align: center; font-size: 46px;
  }
  .front-web {
    position: absolute; left: 0; right: 0; top: 186px;
    text-align: center;
    font-family: "Roboto", sans-serif; font-size: 12px;
    letter-spacing: 2.5px; color: var(--silver-dim);
  }

  /* back */
  .back-brand {
    position: absolute; left: 34px; top: 92px; width: 240px;
    text-align: center; font-size: 30px;
  }
  .divider {
    position: absolute; left: 290px; top: 70px;
    width: 1px; height: 120px; background: var(--silver-dim);
  }
  .person { position: absolute; left: 312px; top: 78px; }
  .person-name {
    font-family: "Cormorant Garamond", serif; font-weight: 500;
    font-size: 20px; letter-spacing: 1px; text-transform: uppercase;
  }
  .person-title {
    font-family: "Roboto", sans-serif; font-size: 12px;
    color: var(--silver-dim); margin-top: 2px;
  }
  .contact-list { list-style: none; margin-top: 14px; }
  .contact-list li, .address {
    display: flex; align-items: center; gap: 7px;
    font-family: "Roboto", sans-serif; font-size: 11.5px;
    line-height: 19px; color: var(--silver);
  }
  .icon { width: 12px; height: 12px; flex: none; }
  .address { position: absolute; left: 34px; bottom: 36px; }
</style>
</head>
<body>

<section class="card card--front">
  <div class="brand-name front-brand">Wandering Rooms</div>
  <div class="front-web">www.wanderingrooms-example.com</div>
</section>

<section class="card card--back">
  <div class="brand-name back-brand">Wandering Rooms</div>
  <div class="divider"></div>

  <div class="person">
    <div class="person-name">Marcus Hale</div>
    <div class="person-title">Gerente General</div>
    <ul class="contact-list">
      <li>
        <svg class="icon" viewBox="0 0 12 12"><circle cx="6" cy="6" r="6" fill="#c9c7c2"/><path d="M4 3.2l1 .1.5 1.4-.7.6c.3.7.8 1.2 1.5 1.5l.6-.7 1.4.5.1 1c-.3.5-.8.7-1.3.6C5 7.8 4.2 7 3.6 5c-.1-.6.1-1.3.4-1.8z" fill="#0d0d0d"/></svg>
        +971 2 518 2047
      </li>
      <li>
        <svg class="icon" viewBox="0 0 12 12"><circle cx="6" cy="6" r="6" fill="#c9c7c2"/><rect x="3" y="4" width="6" height="4.2" fill="none" stroke="#0d0d0d" stroke-width=".8"/><path d="M3 4l3 2.3L9 4" fill="none" stroke="#0d0d0d" stroke-width=".8"/></svg>
        info@wanderingrooms-example.com
      </li>
      <li>
        <svg class="icon" viewBox="0 0 12 12"><circle cx="6" cy="6" r="6" fill="#c9c7c2"/><circle cx="6" cy="6" r="3" fill="none" stroke="#0d0d0d" stroke-width=".8"/><path d="M3 6h6M6 3c-1.3 1.6-1.3 4.4 0 6M6 3c1.3 1.6 1.3 4.4 0 6" fill="none" stroke="#0d0d0d" stroke-width=".7"/></svg>
        www.wanderingrooms-example.com
      </li>
    </ul>
  </div>

  <div class="address">
    <svg class="icon" viewBox="0 0 12 12"><circle cx="6" cy="6" r="6" fill="#c9c7c2"/><path d="M6 2.8a2 2 0 0 1 2 2c0 1.4-2 3.8-2 3.8S4 6.2 4 4.8a2 2 0 0 1 2-2z" fill="#0d0d0d"/><circle cx="6" cy="4.8" r=".7" fill="#c9c7c2"/></svg>
    Block C&amp;D, Bldg. 47, Court 12, Abu Dhabi, United Arab Emirates
  </div>
</section>

</body>
</html>
```